Canadian Christian Church needs design for new sermon series

A graphic design for our series and an invitation card to invite people to the series. Check design brief for more detailed information. Target audience: young families and young adults. Looking for a creative design that will get people's attention and create interest. See design brief for copy of design purchased for previous series.
Updates
entered Apr 4 incorrectly. Need a week to receive and review designs, and today is Apr 2/19. Thanks!
Target Market(s)
young families and young adults
Colors
Designer to choose colors to be used in the design.
Look and feel

```html
<!DOCTYPE html>
<html lang="en">
<head>
<meta charset="utf-8">
<title>Messy – Sermon Series Invitation</title>
<link rel="stylesheet" href="https://fonts.googleapis.com/css2?family=Anton&family=Alfa+Slab+One&family=Roboto+Slab:wght@400;700&family=Montserrat:wght@400;500;600&display=swap">
<style>
  :root {
    --backdrop: #7a7a7a;
    --band: #3d302b;
    --band-text: #ffffff;
    --orange: #f7941d;
    --orange-light: #ffc23a;
    --outline: #4a2a6a;
    --card-beige: #cec5ad;
    --card-beige-light: #ddd6c2;
    --ink: #2e2824;
    --rule: #5b524a;
    --value-orange: #f39020;
    --value-blue: #1d78c1;
    --value-purple: #8e2b8e;
    --tick-blue: #1d78c1;
    --paper-white: #eeebe6;
    --paper-grey: #c9c5be;
    --paper-yellow: #efe0a4;
    --paper-peach: #efc29e;
    --paper-pink: #e7a9b8;
  }
  * { box-sizing: border-box; margin: 0; padding: 0; }
  html, body { width: 1200px; height: 903px; overflow: hidden; }
  body { background: var(--backdrop); position: relative; font-family: "Montserrat", sans-serif; }

  .card { position: absolute; width: 483px; height: 377px; overflow: hidden; box-shadow: 0 3px 8px rgba(0,0,0,.35); }
  .card--front { left: 237px; top: 61px; }
  .card--back { left: 582px; top: 470px; background: radial-gradient(ellipse at 70% 40%, var(--card-beige-light), var(--card-beige) 70%); }

  /* front */
  .hero-photo { position: absolute; inset: 0 0 42px 0;
    background:
      radial-gradient(ellipse 70px 110px at 49% 52%, rgba(255,255,255,.95), rgba(255,255,255,0) 100%),
      radial-gradient(ellipse 90px 60px at 12% 18%, rgba(239,194,158,.8), rgba(239,194,158,0) 100%),
      radial-gradient(ellipse 80px 60px at 88% 8%, rgba(231,169,184,.8), rgba(231,169,184,0) 100%),
      radial-gradient(ellipse 100px 70px at 15% 70%, rgba(239,224,164,.85), rgba(239,224,164,0) 100%),
      radial-gradient(ellipse 90px 70px at 80% 78%, rgba(231,169,184,.75), rgba(231,169,184,0) 100%),
      radial-gradient(ellipse 110px 80px at 92% 45%, rgba(239,194,158,.75), rgba(239,194,158,0) 100%),
      radial-gradient(ellipse 90px 60px at 40% 88%, rgba(239,224,164,.8), rgba(239,224,164,0) 100%),
      radial-gradient(ellipse 80px 60px at 60% 20%, rgba(239,224,164,.7), rgba(239,224,164,0) 100%),
      linear-gradient(160deg, var(--paper-white), var(--paper-grey) 55%, var(--paper-white)); }
  .church-name { position: absolute; left: 30px; top: 96px; display: flex; align-items: center; gap: 6px;
    font-family: "Roboto Slab", serif; font-size: 12px; color: var(--ink); }
  .church-name .dot { width: 12px; height: 12px; border-radius: 50%; background: var(--value-purple); }
  .series-title { position: absolute; right: 26px; top: 14px; font-family: "Anton", sans-serif; font-size: 66px; line-height: 1;
    letter-spacing: 1px; color: var(--orange);
    background: linear-gradient(180deg, var(--orange-light), var(--orange) 60%, #e0611b); -webkit-background-clip: text; background-clip: text;
    -webkit-text-fill-color: transparent; -webkit-text-stroke: 1.5px var(--outline); }
  .series-tagline { position: absolute; left: 0; right: 0; top: 290px; text-align: center; font-family: "Alfa Slab One", serif;
    font-size: 34px; color: var(--orange); -webkit-text-stroke: 1.5px #3a1e0c; letter-spacing: -.5px; white-space: nowrap; }
  .front-band { position: absolute; left: 0; right: 0; bottom: 0; height: 42px; background: var(--band); color: var(--band-text);
    font-family: "Roboto Slab", serif; font-size: 21px; display: flex; align-items: center; justify-content: center; white-space: nowrap; }

  /* back */
  .service-heading { position: absolute; left: 0; right: 0; top: 22px; text-align: center; font-family: "Roboto Slab", serif;
    font-weight: 700; color: var(--ink); white-space: nowrap; }
  .service-heading .line1 { font-size: 25px; line-height: 1.2; }
  .service-heading .line2 { font-size: 26px; line-height: 1.3; }
  .section-label { position: absolute; left: 27px; font-size: 12px; font-weight: 600; color: var(--ink); }
  .section-label--sermons { top: 98px; }
  .section-label--features { top: 256px; }
  .sermon-table { position: absolute; left: 27px; top: 118px; width: 228px; border-collapse: collapse;
    font-size: 11px; color: var(--ink); border: 1px solid var(--rule); }
  .sermon-table td { height: 15.8px; padding: 0 7px; border-bottom: 1px solid var(--rule); white-space: nowrap; line-height: 1; }
  .sermon-table td.date { width: 74px; border-right: 1px solid var(--rule); font-weight: 500; }
  .feature-list { position: absolute; left: 27px; top: 272px; list-style: none; font-size: 11.5px; color: var(--ink); }
  .feature-list li { display: flex; align-items: center; gap: 7px; line-height: 14.6px; white-space: nowrap; }
  .feature-list svg { width: 8px; height: 8px; }
  .core-values { position: absolute; left: 286px; top: 104px; width: 178px; height: 178px; }
  .back-band { position: absolute; left: 0; right: 0; bottom: 0; height: 52px; background: var(--band); color: var(--band-text);
    font-size: 9.4px; text-align: center; display: flex; flex-direction: column; justify-content: center; gap: 7px; white-space: nowrap; }
</style>
</head>
<body>

<section class="card card--front">
  <div class="hero-photo" role="img" aria-label="Stressed young man buried up to his chest in a sea of scattered white, yellow, peach and pink paper documents, hands on his head"></div>
  <div class="church-name"><span class="dot"></span>Maple Grove Family Church</div>
  <h1 class="series-title">MESSY</h1>
  <p class="series-tagline">Joining God in the Mess</p>
  <div class="front-band">Connecting Young Families to Christ</div>
</section>

<section class="card card--back">
  <h2 class="service-heading">
    <span class="line1">THE TIME OF THE SERVICES:</span><br>
    <span class="line2">Sundays @ 10:30</span>
  </h2>

  <p class="section-label section-label--sermons">Names &amp; Dates of the sermons:</p>
  <table class="sermon-table">
    <tr><td class="date">April 28th:</td><td>We Made This Mess</td></tr>
    <tr><td class="date">May 5th:</td><td>Bless in the Mess</td></tr>
    <tr><td class="date">May 12th:</td><td>Born into the Mess</td></tr>
    <tr><td class="date">May 19th:</td><td>Messy Work</td></tr>
    <tr><td class="date">May 26th:</td><td>Messy Church</td></tr>
    <tr><td class="date">June 2nd:</td><td>Messy Hospitality</td></tr>
    <tr><td class="date">June 9th:</td><td>TBD</td></tr>
    <tr><td class="date">June 16th:</td><td>Messy within Boundaries</td></tr>
  </table>

  <svg class="core-values" viewBox="-100 -100 200 200" aria-label="Core values diagram">
    <g transform="rotate(-162)" fill="none" stroke-width="48">
      <circle r="70" pathLength="100" stroke="var(--value-orange)" stroke-dasharray="19.4 80.6" stroke-dashoffset="0"/>
      <circle r="70" pathLength="100" stroke="var(--value-blue)" stroke-dasharray="19.4 80.6" stroke-dashoffset="-20"/>
      <circle r="70" pathLength="100" stroke="var(--value-orange)" stroke-dasharray="19.4 80.6" stroke-dashoffset="-40"/>
      <circle r="70" pathLength="100" stroke="var(--value-purple)" stroke-dasharray="19.4 80.6" stroke-dashoffset="-60"/>
      <circle r="70" pathLength="100" stroke="var(--value-blue)" stroke-dasharray="19.4 80.6" stroke-dashoffset="-80"/>
    </g>
    <g font-family="Montserrat, sans-serif" fill="#ffffff" text-anchor="middle">
      <text x="-41" y="-62" font-size="7.5" font-weight="600">EQUIPPING</text>
      <text x="-41" y="-54" font-size="4.6">preparing people</text>
      <text x="-41" y="-48" font-size="4.6">for the kingdom</text>
      <text x="41" y="-62" font-size="7.5" font-weight="600">SERVING</text>
      <text x="41" y="-54" font-size="4.6">giving our time,</text>
      <text x="41" y="-48" font-size="4.6">talent and treasure</text>
      <text x="67" y="15" font-size="7" font-weight="600">MISSIONAL</text>
      <text x="67" y="22" font-size="7" font-weight="600">LIVING</text>
      <text x="67" y="29" font-size="4.6">pursuing the lost</text>
      <text x="67" y="35" font-size="4.6">where they are</text>
      <text x="0" y="66" font-size="7.5" font-weight="600">SPIRIT-LIVING</text>
      <text x="0" y="74" font-size="4.6">led and empowered</text>
      <text x="0" y="80" font-size="4.6">by the Spirit</text>
      <text x="-67" y="18" font-size="7.5" font-weight="600">BELONGING</text>
      <text x="-67" y="26" font-size="4.6">a caring family</text>
      <text x="-67" y="32" font-size="4.6">environment</text>
    </g>
    <text x="0" y="-2" text-anchor="middle" font-family="Montserrat, sans-serif" font-size="10" fill="var(--ink)">CORE</text>
    <text x="0" y="10" text-anchor="middle" font-family="Montserrat, sans-serif" font-size="10" fill="var(--ink)">VALUES</text>
  </svg>

  <p class="section-label section-label--features">Features of the service:</p>
  <ul class="feature-list">
    <li><svg viewBox="0 0 10 10"><circle cx="5" cy="5" r="5" fill="var(--tick-blue)"/><path d="M2.8 5.2 4.4 6.7 7.3 3.6" stroke="#fff" stroke-width="1.4" fill="none"/></svg>Staffed nursery &amp; children’s program every Sunday</li>
    <li><svg viewBox="0 0 10 10"><circle cx="5" cy="5" r="5" fill="var(--tick-blue)"/><path d="M2.8 5.2 4.4 6.7 7.3 3.6" stroke="#fff" stroke-width="1.4" fill="none"/></svg>Coffee &amp; snacks</li>
    <li><svg viewBox="0 0 10 10"><circle cx="5" cy="5" r="5" fill="var(--tick-blue)"/><path d="M2.8 5.2 4.4 6.7 7.3 3.6" stroke="#fff" stroke-width="1.4" fill="none"/></svg>Everyone welcome</li>
  </ul>

  <footer class="back-band">
    <span>Location - 1875 Cedar Ridge Road Oakville, ON L6M 2T4</span>
    <span>Phone-905-555-0142 | Email-info@maplegrovechurch.ca | Website-www.maplegrovechurch.ca</span>
  </footer>
</section>

</body>
</html>
```